Lar Ventura Banners Ads

We need to create 4 animated banners ads in GIF (3 arts for each banner) to Lar Ventura Publiclik Display Campaign
Lar Ventura is an ecommerce in Brazil that sells high end home products.
It is a Branding Campaign, but we will add products images on it, so it has to be very sofisticated like the brand is.

We need 4 designs - 1 design for each size:

- Retângulo inline (300 X 250)
- Retângulo grande (336 x 280)
- Banner (468 x 60)
- Cabeçalho (728 x 90)

Please, find the briefing in pdf archive attached

Text we can work on th banners:

1 - Sofisticação com exclusividade para sua Casa!
2 - chique, exclusivo e encantador
3 - Encantador, sofisticado e exclusivo

The final image has to have Fontenelle´s Logo, Lar Ventura´s logo and a call to action:

Confira nossos produtos exclusivos!

_________________________________________________________________
UPDATE

Please, for the colors, take the ones from pdf; (use more collors chics, silver and white, but not only this colors);
Don't forget the CALL TO ACTION " Confira nossos Produtos Exclusivos!"

If you'd like to meet the brand and the target, here is the page on Facebook: https://www.rededeamigos.example/LarVenturaHomeVentura

But please, DO NOT COPY ANY OF THESE EXAMPLES ON THE PAGE.
We need something more executive.

Target Market(s)

Woman 30+
Trendy, modern, sofisticated, married or mum, cosmopolitan,
UPPERCLASS

Industry/Entity Type

Call

Font styles to use
Script
Other font styles liked:
• ColfaxTrial

Requirements
Must have
• Product images
Text
Product Image + Call to action on final layer with logos
As you will see the example in pdf archive attached
Nice to have
• frames
Should not have
• people
flowers
girlish drawing

```html
<!DOCTYPE html>
<html lang="pt-BR">
<head>
<meta charset="utf-8">
<title>Lar Ventura — Banners Display</title>
<link rel="stylesheet" href="https://fonts.googleapis.com/css2?family=Roboto:wght@400&family=Roboto+Condensed:wght@700&display=swap">
<style>
  :root{
    --board:#f3f3f2;
    --frame:#d9d7d3;
    --wall-light:#cfcdc8;
    --wall-mid:#b9b7b2;
    --wall-dark:#a4a29c;
    --cream:#efece6;
    --taupe:#a0968b;
    --taupe-dark:#7d746a;
    --logo:#8a8076;
    --headline:#ffffff;
    --note:#b3121b;
    --towel-grey:#b9bcc3;
    --towel-pink:#dcc6c3;
    --towel-blue:#a9c2d5;
    --towel-navy:#353b48;
    --chair-wood:#8d6c50;
  }
  html,body{margin:0;padding:0;width:1200px;height:800px;overflow:hidden;background:var(--board);}
  .canvas{position:relative;width:1200px;height:800px;overflow:hidden;background:var(--board);}
  .board{position:absolute;left:0;top:0;width:820px;height:547px;transform:scale(1.4634,1.4625);transform-origin:0 0;}
  .banner{position:absolute;overflow:hidden;box-shadow:0 0 0 1px var(--frame);}
  .banner svg{position:absolute;left:0;top:0;width:100%;height:100%;display:block;}
  .headline{position:absolute;margin:0;color:var(--headline);font-family:"Roboto",Arial,sans-serif;font-weight:400;white-space:nowrap;text-shadow:0 1px 2px rgba(90,88,84,.35);}
  .brand{position:absolute;margin:0;color:var(--logo);font-family:"Roboto",Arial,sans-serif;font-weight:400;text-transform:uppercase;white-space:nowrap;text-align:center;}

  .leaderboard{left:46px;top:27px;width:727px;height:89px;}
  .leaderboard .headline{left:34px;top:5px;font-size:24px;line-height:25.5px;}
  .leaderboard .brand{left:468px;width:259px;top:27px;font-size:28px;line-height:34px;letter-spacing:2px;}

  .banner-full{left:46px;top:131px;width:467px;height:60px;}
  .banner-full .headline{left:18px;top:3px;font-size:16px;line-height:17px;}
  .banner-full .brand{left:296px;width:171px;top:18px;font-size:20px;line-height:24px;letter-spacing:1.4px;}

  .rect-large{left:46px;top:207px;width:336px;height:279px;}
  .rect-large .headline{left:14px;top:23px;font-size:26px;line-height:29.5px;}
  .rect-large .brand{left:0;width:336px;top:239px;font-size:32px;line-height:36px;letter-spacing:2.4px;}

  .rect-inline{left:397px;top:207px;width:299px;height:249px;}
  .rect-inline .headline{left:12px;top:21px;font-size:23px;line-height:27.5px;}
  .rect-inline .brand{left:0;width:299px;top:213px;font-size:28px;line-height:32px;letter-spacing:2px;}

  .note{position:absolute;left:0;top:502px;width:820px;margin:0;text-align:center;color:var(--note);font-family:"Roboto Condensed","Arial Narrow",sans-serif;font-weight:700;font-size:20px;letter-spacing:.2px;}
</style>
</head>
<body>
<div class="canvas">
  <div class="board">

    <section class="banner leaderboard" aria-label="Cabeçalho 728 x 90">
      <svg viewBox="0 0 727 89" preserveAspectRatio="none">
        <defs>
          <linearGradient id="wall-lb" x1="0" x2="1" y1="0" y2="0">
            <stop offset="0" stop-color="var(--wall-light)"/>
            <stop offset=".7" stop-color="var(--wall-mid)"/>
            <stop offset="1" stop-color="var(--wall-dark)"/>
          </linearGradient>
          <linearGradient id="towels-lb" x1="0" x2="0" y1="0" y2="1">
            <stop offset="0" stop-color="var(--towel-grey)"/>
            <stop offset=".3" stop-color="var(--towel-pink)"/>
            <stop offset=".55" stop-color="var(--towel-blue)"/>
            <stop offset=".78" stop-color="var(--towel-navy)"/>
            <stop offset="1" stop-color="var(--chair-wood)"/>
          </linearGradient>
        </defs>
        <rect width="727" height="89" fill="url(#wall-lb)"/>
        <rect class="product-photo" x="338" y="6" width="128" height="83" rx="6" fill="url(#towels-lb)" role="img" aria-label="Pilha de toalhas dobradas em tons pastel sobre uma cadeira de madeira"/>
        <path class="panel" d="M0 0H38C18 25 14 60 30 89H0Z" fill="var(--cream)"/>
        <path d="M38 0C18 25 14 60 30 89" fill="none" stroke="var(--taupe)" stroke-width="2"/>
        <path class="panel" d="M462 0C448 25 452 60 476 89H727V0Z" fill="var(--cream)"/>
        <path d="M462 0C448 25 452 60 476 89" fill="none" stroke="var(--taupe-dark)" stroke-width="3"/>
      </svg>
      <p class="headline">Sofisticação com<br>exclusividade<br>para sua Casa!</p>
      <p class="brand">Lar Ventura</p>
    </section>

    <section class="banner banner-full" aria-label="Banner 468 x 60">
      <svg viewBox="0 0 467 60" preserveAspectRatio="none">
        <defs>
          <linearGradient id="wall-bn" x1="0" x2="1" y1="0" y2="0">
            <stop offset="0" stop-color="var(--wall-light)"/>
            <stop offset=".7" stop-color="var(--wall-mid)"/>
            <stop offset="1" stop-color="var(--wall-dark)"/>
          </linearGradient>
          <linearGradient id="towels-bn" x1="0" x2="0" y1="0" y2="1">
            <stop offset="0" stop-color="var(--towel-grey)"/>
            <stop offset=".3" stop-color="var(--towel-pink)"/>
            <stop offset=".55" stop-color="var(--towel-blue)"/>
            <stop offset=".78" stop-color="var(--towel-navy)"/>
            <stop offset="1" stop-color="var(--chair-wood)"/>
          </linearGradient>
        </defs>
        <rect width="467" height="60" fill="url(#wall-bn)"/>
        <rect class="product-photo" x="210" y="4" width="88" height="56" rx="5" fill="url(#towels-bn)" role="img" aria-label="Pilha de toalhas dobradas em tons pastel sobre uma cadeira de madeira"/>
        <path class="panel" d="M0 0H12C5 20 5 40 14 60H0Z" fill="var(--cream)"/>
        <path d="M12 0C5 20 5 40 14 60" fill="none" stroke="var(--taupe)" stroke-width="1.5"/>
        <path class="panel" d="M296 0C284 18 286 42 302 60H467V0Z" fill="var(--cream)"/>
        <path d="M296 0C284 18 286 42 302 60" fill="none" stroke="var(--taupe-dark)" stroke-width="2.5"/>
      </svg>
      <p class="headline">Sofisticação com<br>exclusividade<br>para sua Casa!</p>
      <p class="brand">Lar Ventura</p>
    </section>

    <section class="banner rect-large" aria-label="Retângulo grande 336 x 280">
      <svg viewBox="0 0 336 279" preserveAspectRatio="none">
        <defs>
          <linearGradient id="wall-rl" x1="0" x2="1" y1="0" y2="1">
            <stop offset="0" stop-color="var(--wall-light)"/>
            <stop offset=".6" stop-color="var(--wall-mid)"/>
            <stop offset="1" stop-color="var(--wall-dark)"/>
          </linearGradient>
          <linearGradient id="towels-rl" x1="0" x2="0" y1="0" y2="1">
            <stop offset="0" stop-color="var(--towel-grey)"/>
            <stop offset=".28" stop-color="var(--towel-pink)"/>
            <stop offset=".52" stop-color="var(--towel-blue)"/>
            <stop offset=".72" stop-color="var(--towel-navy)"/>
            <stop offset="1" stop-color="var(--chair-wood)"/>
          </linearGradient>
        </defs>
        <rect width="336" height="279" fill="url(#wall-rl)"/>
        <rect class="product-photo" x="118" y="82" width="218" height="150" rx="10" fill="url(#towels-rl)" role="img" aria-label="Pilha de toalhas dobradas em tons pastel sobre uma cadeira de madeira"/>
        <path class="panel" d="M0 0H336V8C250 30 120 0 0 22Z" fill="var(--cream)"/>
        <path d="M336 8C250 30 120 0 0 22" fill="none" stroke="var(--taupe)" stroke-width="2.5"/>
        <path class="panel" d="M0 236C110 215 230 226 336 196V279H0Z" fill="var(--cream)"/>
        <path d="M0 236C110 215 230 226 336 196" fill="none" stroke="var(--taupe-dark)" stroke-width="3"/>
      </svg>
      <p class="headline">Sofisticação com<br>exclusividade<br>para sua Casa!</p>
      <p class="brand">Lar Ventura</p>
    </section>

    <section class="banner rect-inline" aria-label="Retângulo inline 300 x 250">
      <svg viewBox="0 0 299 249" preserveAspectRatio="none">
        <defs>
          <linearGradient id="wall-ri" x1="0" x2="1" y1="0" y2="1">
            <stop offset="0" stop-color="var(--wall-light)"/>
            <stop offset=".6" stop-color="var(--wall-mid)"/>
            <stop offset="1" stop-color="var(--wall-dark)"/>
          </linearGradient>
          <linearGradient id="towels-ri" x1="0" x2="0" y1="0" y2="1">
            <stop offset="0" stop-color="var(--towel-grey)"/>
            <stop offset=".28" stop-color="var(--towel-pink)"/>
            <stop offset=".52" stop-color="var(--towel-blue)"/>
            <stop offset=".72" stop-color="var(--towel-navy)"/>
            <stop offset="1" stop-color="var(--chair-wood)"/>
          </linearGradient>
        </defs>
        <rect width="299" height="249" fill="url(#wall-ri)"/>
        <rect class="product-photo" x="110" y="72" width="189" height="135" rx="9" fill="url(#towels-ri)" role="img" aria-label="Pilha de toalhas dobradas em tons pastel sobre uma cadeira de madeira"/>
        <path class="panel" d="M0 0H299V6C220 28 100 -2 0 20Z" fill="var(--cream)"/>
        <path d="M299 6C220 28 100 -2 0 20" fill="none" stroke="var(--taupe)" stroke-width="2.5"/>
        <path class="panel" d="M0 212C100 190 200 206 299 178V249H0Z" fill="var(--cream)"/>
        <path d="M0 212C100 190 200 206 299 178" fill="none" stroke="var(--taupe-dark)" stroke-width="3"/>
      </svg>
      <p class="headline">Sofisticação com<br>exclusividade<br>para sua Casa!</p>
      <p class="brand">Lar Ventura</p>
    </section>

    <p class="note">SEE THE LINKS IN THE DESCRIPTION TO VIEW THE ANIMATION</p>
  </div>
</div>
</body>
</html>
```